Personal Blog

The wordpress blog style and layout should be similar to http://www.samfenwick.com

homepage: my photo, list of things, call to action then 3 boxes (The Blog, The Book and podcast)

Other pages: About us, Blog, Consulting, Contact

Target Market(s)

Web Marketing Consultant

Industry/Entity Type

Consulting

Colors
3277b5
33a6d7
f04a50
f68e4e
33b7a4

```html
<!DOCTYPE html>
<html lang="en">
<head>
<meta charset="utf-8">
<title>Rami Haddad – Contact</title>
<link href="https://fonts.googleapis.com/css2?family=Dosis:wght@500;600&family=Arimo:ital,wght@0,400;0,700;1,700&display=swap" rel="stylesheet">
<style>
:root{
  --navy:#1c2331;
  --navy-deep:#151a25;
  --orange:#f68e4e;
  --page:#e8edf0;
  --panel:#ffffff;
  --band:#eef2f5;
  --line:#d9dee2;
  --ink:#222831;
  --muted:#8a9096;
  --blue:#3277b5;
  --sky:#33a6d7;
  --red:#f04a50;
  --teal:#33b7a4;
  --white:#ffffff;
}
*{box-sizing:border-box;margin:0;padding:0}
html,body{width:1200px;height:2673px;overflow:hidden}
body{position:relative;background:var(--page);font-family:"Arimo",Arial,sans-serif;color:var(--ink)}
.abs{position:absolute}
h1,h2,h3,.nav a,.btn{font-family:"Dosis","Arial Narrow",sans-serif;font-weight:600}
p{font-size:17px;line-height:25px}

/* header */
.site-header{left:0;top:0;width:1200px;height:138px;background:var(--navy)}
.brand{left:48px;top:50px;display:flex;align-items:center;gap:16px}
.brand-mark{width:40px;height:40px;background:var(--orange);border-radius:4px}
.brand-name{font-family:"Dosis",sans-serif;font-weight:600;font-size:38px;color:var(--white)}
.nav{left:538px;top:56px}
.nav a{color:var(--white);text-decoration:none;font-size:22px;position:absolute;white-space:nowrap}
.nav a.current{color:var(--orange)}

/* main panel */
.main-panel{left:48px;top:184px;width:726px;height:1871px;background:var(--panel);border:1px solid var(--line)}
.section-title{font-size:29px;color:var(--ink);letter-spacing:.5px}
.contact-box{left:83px;top:350px;width:648px;height:660px;border:1px solid var(--line);background:#fafbfc}
.map{left:92px;top:362px;width:633px;height:372px;background:linear-gradient(135deg,#dfe6ea,#b8c9d3 60%,#a8bfd0)}
.detail{font-size:16px;color:var(--ink);display:flex;align-items:center;gap:22px}
.detail svg{flex:none}
.social-row{left:83px;width:650px;display:flex;gap:24px;align-items:flex-start}
.social-row .sq{width:58px;height:58px;border-radius:4px;flex:none}
.social-row p{font-size:16px;line-height:24px;margin-top:2px}
.band{left:48px;top:1338px;width:726px;height:134px;background:var(--band)}
.field{border:1px solid #cdd2d6;border-radius:6px;background:var(--white);font-size:14px;color:#9aa0a5;padding:0 20px;display:flex;align-items:center}
.btn{background:var(--orange);color:var(--white);border-radius:5px;display:flex;align-items:center;justify-content:center;font-size:26px;letter-spacing:1px}

/* sidebar */
.about-card{left:807px;top:184px;width:357px;height:603px;background:var(--panel);border:1px solid var(--line)}
.portrait{left:872px;top:205px;width:226px;height:226px;border-radius:50%;background:radial-gradient(circle at 50% 40%,#dde3ea,#b9c4d0);border:6px solid #eef1f4}
.about-text{left:830px;top:502px;width:311px;text-align:center;font-size:16px;line-height:24px;color:var(--muted)}
.about-text em{color:var(--orange);font-weight:700}
.bootcamp{left:807px;top:837px;width:357px;height:514px;background:var(--navy)}
.ad{left:807px;width:357px}
.ad-retreat{top:1402px;height:350px;background:linear-gradient(180deg,#4fb2d8,#93cfe2 45%,#d9b88d)}
.ad-team{top:1791px;height:297px;background:linear-gradient(160deg,#ffffff,#d6eef4 55%,#e2543a)}

/* footer */
.site-footer{left:0;top:2337px;width:1200px;height:336px;background:var(--navy)}
.footer-base{left:0;top:2600px;width:1200px;height:73px;background:var(--navy-deep)}
.footer-title{color:var(--white);font-size:27px;letter-spacing:.5px;white-space:nowrap}
.footer-text{color:var(--white);font-size:14px;line-height:20px}
.footer-link{color:var(--orange)}
.net{width:57px;height:57px;border-radius:4px;background:#8c7d6a}
.copy{left:0;top:2618px;width:1200px;text-align:center;color:var(--white);font-size:14px}
</style>
</head>
<body>

<header class="site-header abs">
  <div class="brand abs"><span class="brand-mark"></span><span class="brand-name">Rami Haddad</span></div>
  <nav class="nav abs">
    <a style="left:0">ABOUT</a>
    <a style="left:92px">BLOG</a>
    <a style="left:175px">CONSULTING</a>
    <a style="left:314px">RESOURCES</a>
    <a style="left:452px">BOOK</a>
    <a class="current" style="left:534px">CONTACT</a>
  </nav>
</header>

<main>
  <div class="main-panel abs"></div>

  <h1 class="section-title abs" style="left:83px;top:210px">GET IN TOUCH</h1>
  <p class="abs" style="left:83px;top:255px;width:650px">Lorem ipsum dolor sit amet, con sectetur adipiscing elit, sed do ei usmod tempor incididunt ut labo re et dolore magna aliqua.</p>

  <div class="contact-box abs"></div>
  <div class="map abs" role="img" aria-label="Street map showing the office location by the bay"></div>
  <h2 class="section-title abs" style="left:104px;top:766px;font-size:27px">Contact Details</h2>
  <div class="detail abs" style="left:104px;top:826px">
    <svg width="28" height="28" viewBox="0 0 28 28"><rect width="28" height="28" rx="3" fill="var(--orange)"/><path d="M14 6a6 6 0 0 0-6 6c0 5 6 10 6 10s6-5 6-10a6 6 0 0 0-6-6zm0 8.5a2.5 2.5 0 1 1 0-5 2.5 2.5 0 0 1 0 5z" fill="#fff"/></svg>Lorem Street - 6, dolor site</div>
  <div class="detail abs" style="left:104px;top:868px">
    <svg width="28" height="28" viewBox="0 0 28 28"><path d="M7 16c4-6 10-6 14 0l-3 2-2-3h-4l-2 3z" fill="var(--orange)"/><rect x="8" y="18" width="12" height="5" rx="1" fill="var(--orange)"/></svg>+01- 123 - 456 - 7890</div>
  <div class="detail abs" style="left:424px;top:826px">
    <svg width="28" height="28" viewBox="0 0 28 28"><rect x="3" y="7" width="22" height="15" rx="2" fill="var(--orange)"/><path d="M3 8l11 8 11-8" stroke="#fff" stroke-width="2" fill="none"/></svg>rami.haddad@example.com</div>
  <div class="detail abs" style="left:424px;top:868px">
    <svg width="28" height="28" viewBox="0 0 28 28"><circle cx="14" cy="14" r="11" fill="var(--orange)"/><rect x="8" y="10" width="12" height="9" fill="#fff"/></svg>+01- 123 - 456 - 7890</div>

  <h2 class="section-title abs" style="left:83px;top:1030px;width:680px;font-size:28px;line-height:38px">Also, I'd like you to consider contacting me via social media, instead:</h2>
  <div class="social-row abs" style="top:1110px"><span class="sq" style="background:var(--blue)" aria-label="Friendbook"></span><p>Lorem ipsum dolor sit amet, con sectetur adipiscing elit, sed do ei usmod tempor incididunt ut labo re et dolore magna aliqua.</p></div>
  <div class="social-row abs" style="top:1188px"><span class="sq" style="background:var(--sky)" aria-label="Chirper"></span><p>Lorem ipsum dolor sit amet, con sectetur adipiscing elit, sed do ei usmod tempor incididunt ut labo re et dolore magna aliqua.</p></div>
  <div class="social-row abs" style="top:1266px"><span class="sq" style="background:var(--red)" aria-label="Circles"></span><p>Lorem ipsum dolor sit amet, con sectetur adipiscing elit, sed do ei usmod tempor incididunt ut labo re et dolore magna aliqua.</p></div>

  <div class="band abs"></div>
  <h2 class="section-title abs" style="left:83px;top:1352px">Interview Requests</h2>
  <p class="abs" style="left:83px;top:1396px;width:650px">Lorem ipsum dolor sit amet, con sectetur adipiscing elit, sed do ei usmod tempor incididunt ut labo re et dolore magna aliqua.</p>

  <h2 class="section-title abs" style="left:83px;top:1514px">Send a message</h2>
  <p class="abs" style="left:83px;top:1558px;width:650px">Lorem ipsum dolor sit amet, con sectetur adipiscing elit, sed do ei usmod tempor incididunt ut labo re et dolore magna aliqua.</p>

  <div class="field abs" style="left:83px;top:1657px;width:306px;height:58px">Name</div>
  <div class="field abs" style="left:83px;top:1726px;width:306px;height:58px">Email</div>
  <div class="field abs" style="left:83px;top:1797px;width:306px;height:58px">Subject</div>
  <div class="field abs" style="left:410px;top:1657px;width:324px;height:193px;align-items:flex-start;padding-top:22px">Email</div>
  <div class="btn abs" style="left:83px;top:1880px;width:651px;height:53px">SEND</div>
</main>

<aside>
  <div class="about-card abs"></div>
  <div class="portrait abs" role="img" aria-label="Portrait photo of Rami Haddad"></div>
  <h2 class="section-title abs" style="left:807px;top:456px;width:357px;text-align:center;font-size:28px">ABOUT ME</h2>
  <p class="about-text abs">Lorem ipsum dolor sit amet, con sectetur adipiscing elit, sed do ei usmod tempor incididunt ut labo re et dolore magna aliqua. Ut enim ad minim veniam, quis nos exer citation ullamco laboris nisi ut aliq uip ex ea commodo conseq. Read more about/get in touch with me <em>Click here</em></p>

  <div class="bootcamp abs"></div>
  <h2 class="abs" style="left:843px;top:862px;width:300px;color:var(--white);font-size:27px;line-height:33px">JOIN MY NEW BUSINESS BOOTCAMP FOR FREE</h2>
  <p class="abs" style="left:843px;top:952px;width:290px;color:var(--white);font-size:16px;line-height:24px">Learn how to create raving fans with free eBooks, get started with online video and podcasting, engage with social media and blog your way to business success, plus much more!</p>
  <div class="field abs" style="left:843px;top:1143px;width:282px;height:52px">Enter your name...</div>
  <div class="field abs" style="left:843px;top:1209px;width:282px;height:52px">Enter your email...</div>
  <div class="btn abs" style="left:843px;top:1283px;width:282px;height:42px;font-size:25px">JOIN FOR FREE!</div>

  <div class="ad ad-retreat abs" role="img" aria-label="Banner for the Island Ideas Retreat with speaker photos on a beach"></div>
  <div class="ad ad-team abs" role="img" aria-label="Banner for Remote Team Match, a virtual assistant hiring service"></div>

  <div class="field abs" style="left:807px;top:2124px;width:357px;height:53px">Search Archive</div>
  <div class="btn abs" style="left:807px;top:2192px;width:158px;height:48px;font-size:25px">SEARCH</div>
</aside>

<footer>
  <div class="site-footer abs"></div>
  <div class="footer-base abs"></div>

  <h3 class="footer-title abs" style="left:48px;top:2376px">ENTREPRENEUR, SPEAKER,</h3>
  <p class="footer-text abs" style="left:48px;top:2426px;width:330px">Lorem Ipsum is simply dummy text of the printing &amp; typesetting industry. Lorem Ipsum has been industry's standard dummy text ever since the 1500s.</p>
  <p class="footer-text abs" style="left:48px;top:2510px;width:330px">Lorem Ipsum is simply dummy text of the printing &amp; typesetting industry.</p>
  <p class="footer-text footer-link abs" style="left:48px;top:2552px">[ Read the long-winded version! ]</p>

  <h3 class="footer-title abs" style="left:422px;top:2376px">JOIN MY NEW BUSINESS</h3>
  <div class="field abs" style="left:422px;top:2430px;width:335px;height:42px;color:#333;border-radius:2px">Enter your name...</div>
  <div class="field abs" style="left:422px;top:2483px;width:335px;height:42px;color:#333;border-radius:2px">Enter your email...</div>
  <div class="btn abs" style="left:422px;top:2540px;width:335px;height:47px;font-size:27px">JOIN FOR FREE!</div>

  <h3 class="footer-title abs" style="left:799px;top:2376px">CONNECT WITH ME</h3>
  <div class="abs" style="left:799px;top:2430px;display:flex;gap:16px">
    <span class="net" style="background:var(--orange)" aria-label="Friendbook"></span>
    <span class="net" aria-label="Chirper"></span>
    <span class="net" aria-label="Feed"></span>
    <span class="net" aria-label="Clipcast"></span>
  </div>
  <p class="footer-text abs" style="left:799px;top:2512px;width:290px;text-align:center">OR</p>
  <p class="footer-text abs" style="left:799px;top:2534px;width:290px;text-align:center">Connect with via <span class="footer-link">email</span></p>

  <p class="copy abs">© 2014 R. Haddad <span class="footer-link">www.ramihaddad.com</span> | All Right Reserved.</p>
</footer>

</body>
</html>
```